Convention Display

We need a convention booth design for an 10' W x 8' T booth. It should match the look and feel of our website and our brochure design. Sample design and text via 'upload files' below. www.corvantaplume.com

```html
<!DOCTYPE html>
<html lang="en">
<head>
<meta charset="utf-8">
<title>Corvanta Plume – Convention Display</title>
<link rel="stylesheet" href="https://fonts.googleapis.com/css2?family=Oswald:wght@600&family=Questrial&family=Roboto:wght@400;700&family=Kaushan+Script&display=swap">
<style>
  :root {
    --paper: #ffffff;
    --frame: #cfcfcf;
    --ink: #1d1d1d;
    --brand-ink: #3d4a52;
    --muted: #6a6a6a;
    --plus: #a9a9a9;
    --green: #8cc63f;
    --blue: #0f6db7;
    --orange: #f7901e;
    --photo-dark: #8a8a8a;
    --photo-light: #e6e6e6;
  }
  * { margin: 0; padding: 0; box-sizing: border-box; }
  html, body { width: 1200px; height: 848px; overflow: hidden; background: var(--paper); }
  .booth { position: relative; width: 1200px; height: 848px; background: var(--paper); }
  .booth__frame {
    position: absolute; left: 71px; top: 78px; width: 1063px; height: 640px;
    border: 1.5px solid var(--frame);
  }
  .photo {
    position: absolute;
    background: radial-gradient(ellipse at 50% 45%, var(--photo-dark) 0%, #b5b5b5 40%, var(--photo-light) 65%, rgba(255,255,255,0) 78%);
  }
  .photo--clinician { left: 92px; top: 60px; width: 400px; height: 470px; }
  .photo--patient { left: 800px; top: 50px; width: 320px; height: 490px; }

  .headline {
    position: absolute; left: 0; width: 1214px; top: 88px; text-align: center;
    font-family: "Oswald", "Arial Narrow", sans-serif; font-weight: 600; font-size: 25px;
    color: var(--ink); letter-spacing: 0.2px; line-height: 1;
  }
  .headline__accent { color: var(--green); }

  .brand {
    position: absolute; left: 412px; width: 410px; top: 172px; text-align: center;
    font-family: "Roboto", Arial, sans-serif; font-weight: 700; font-size: 54px;
    color: var(--brand-ink); letter-spacing: -1px; line-height: 1;
  }
  .brand__tagline {
    position: absolute; left: 400px; width: 430px; top: 240px; text-align: center;
    font-family: "Roboto", Arial, sans-serif; font-size: 19px; color: var(--ink);
    letter-spacing: 0.4px; line-height: 1;
  }

  .layer-badge {
    position: absolute; width: 124px; height: 124px; border-radius: 50%;
    display: flex; align-items: center; justify-content: center;
    font-family: "Kaushan Script", cursive; font-size: 54px; color: #fff; line-height: 1;
    padding-bottom: 6px;
  }
  .layer-badge--me { left: 192px; top: 355px; background: var(--green); }
  .layer-badge--we { left: 549px; top: 352px; background: var(--blue); }
  .layer-badge--info { left: 912px; top: 352px; background: var(--orange); font-size: 50px; }

  .plus { position: absolute; width: 40px; height: 40px; }
  .plus--first { left: 413px; top: 397px; }
  .plus--second { left: 761px; top: 397px; }

  .layer-motto {
    position: absolute; width: 340px; text-align: center;
    font-family: "Questrial", sans-serif; font-size: 32px; line-height: 1;
  }
  .layer-motto--personal { left: 84px; top: 491px; color: var(--green); }
  .layer-motto--shared { left: 429px; top: 489px; color: var(--blue); }
  .layer-motto--relevant { left: 801px; top: 484px; color: var(--orange); }

  .benefit {
    position: absolute; font-family: "Roboto", Arial, sans-serif; font-size: 25px;
    color: var(--muted); letter-spacing: -1.2px; line-height: 1; white-space: nowrap;
  }
</style>
</head>
<body>
<main class="booth">
  <div class="booth__frame"></div>

  <div class="photo photo--clinician" role="img" aria-label="Photo of a smiling doctor with a stethoscope holding up a smartphone"></div>
  <div class="photo photo--patient" role="img" aria-label="Photo of a smiling pregnant woman with long wavy hair"></div>

  <h1 class="headline"><span class="headline__accent">3 LAYERS</span> TO ENGAGEMENT</h1>

  <div class="brand">corvanta plume</div>
  <p class="brand__tagline">A NEW GENERATION PATIENT PORTAL</p>

  <div class="layer-badge layer-badge--me">me</div>
  <svg class="plus plus--first" viewBox="0 0 40 40" aria-hidden="true"><path d="M15 2h10v13h13v10H25v13H15V25H2V15h13z" fill="var(--plus)"/></svg>
  <div class="layer-badge layer-badge--we">we</div>
  <svg class="plus plus--second" viewBox="0 0 40 40" aria-hidden="true"><path d="M15 2h10v13h13v10H25v13H15V25H2V15h13z" fill="var(--plus)"/></svg>
  <div class="layer-badge layer-badge--info">info</div>

  <p class="layer-motto layer-motto--personal">make it personal</p>
  <p class="layer-motto layer-motto--shared">make it shared</p>
  <p class="layer-motto layer-motto--relevant">make it relevant</p>

  <p class="benefit" style="left:88px;top:572px">Improve Satisfaction</p>
  <p class="benefit" style="left:200px;top:606px">Integrate Your PHR</p>
  <p class="benefit" style="left:127px;top:640px">Change Behavior</p>

  <p class="benefit" style="left:442px;top:572px">Streamline Care</p>
  <p class="benefit" style="left:522px;top:606px">Meet Meaningful Use</p>
  <p class="benefit" style="left:506px;top:640px">Capture Analytics</p>

  <p class="benefit" style="left:795px;top:572px">Increase Donations</p>
  <p class="benefit" style="left:908px;top:606px">Incorporate Staff</p>
  <p class="benefit" style="left:823px;top:640px">Grow Your Community</p>
</main>
</body>
</html>
```